Dunmore Roofing

Want a professional looking business card

Industry/Entity Type

Business

Contact Information for Business Card

Paul Dunmore ( Owner) paul@dunmoreroofing-example.com, www.dunmoreroofing-example.com, Adress: 4172 Township road 43 Plantagenet,ON K9X4T2

```html
<!DOCTYPE html>
<html lang="en">
<head>
<meta charset="utf-8">
<title>Dunmore Roofing — Business Card</title>
<link rel="stylesheet" href="https://fonts.googleapis.com/css2?family=Roboto:wght@400;500;700&family=Roboto+Condensed:wght@400;700&display=swap">
<style>
  :root {
    --backdrop: #2a2a2a;
    --card-white: #f3f3f3;
    --brand-blue: #1b4589;
    --brand-grey: #7a7a7a;
    --back-grey-light: #7c7c7c;
    --back-grey-dark: #6a6a6a;
    --text-white: #ffffff;
    --text-soft: #eeeeee;
  }
  * { box-sizing: border-box; margin: 0; padding: 0; }
  html, body { width: 1200px; height: 960px; overflow: hidden; }
  body {
    background: var(--backdrop);
    font-family: "Roboto", Arial, sans-serif;
    position: relative;
  }
  .card {
    position: absolute;
    width: 600px;
    height: 343px;
    overflow: hidden;
  }
  /* Front */
  .card-front { left: 314px; top: 113px; background: var(--card-white); }
  .card-front .band { position: absolute; left: 0; top: 0; width: 600px; height: 343px; }
  .wordmark {
    position: absolute;
    display: flex;
    align-items: center;
    gap: 10px;
    font-family: "Roboto", Arial, sans-serif;
    font-weight: 700;
    text-transform: uppercase;
    letter-spacing: 1px;
    white-space: nowrap;
  }
  .wordmark .mark { display: block; width: 16px; height: 16px; flex: none; }
  .card-front .wordmark { left: 44px; top: 106px; font-size: 28px; color: var(--brand-blue); }
  .card-front .wordmark .mark { background: var(--brand-blue); }

  .person {
    position: absolute;
    right: 41px;
    top: 215px;
    text-align: right;
    color: var(--text-white);
  }
  .person-name {
    font-family: "Roboto Condensed", "Arial Narrow", sans-serif;
    font-weight: 700;
    font-size: 23px;
    line-height: 1;
    display: flex;
    align-items: center;
    justify-content: flex-end;
    gap: 8px;
  }
  .person-name svg { width: 16px; height: 16px; }
  .person-role { font-size: 15px; font-weight: 400; margin-top: 10px; }
  .address {
    position: absolute;
    right: 41px;
    top: 282px;
    text-align: right;
    font-size: 14.5px;
    line-height: 19px;
    color: var(--text-soft);
  }
  .contacts {
    position: absolute;
    left: 32px;
    top: 262px;
    list-style: none;
    font-size: 14.5px;
    line-height: 19.5px;
    color: var(--text-soft);
  }
  .contacts li { display: flex; align-items: center; gap: 8px; }
  .contacts svg { width: 13px; height: 13px; fill: var(--text-white); flex: none; }

  /* Back */
  .card-back {
    left: 311px; top: 472px;
    background: radial-gradient(ellipse at 50% 35%, var(--back-grey-light), var(--back-grey-dark));
  }
  .card-back .wordmark {
    left: 0; right: 0; top: 150px;
    justify-content: center;
    font-size: 34px;
    color: var(--text-white);
  }
  .card-back .wordmark .mark { background: var(--text-white); width: 20px; height: 20px; }
  .card-back .website {
    position: absolute;
    left: 0; right: 0; top: 285px;
    text-align: center;
    font-size: 14.5px;
    letter-spacing: 4.6px;
    color: var(--text-soft);
  }
</style>
</head>
<body>
  <section class="card card-front" aria-label="Business card front">
    <svg class="band" viewBox="0 0 600 343" aria-hidden="true">
      <polygon points="0,236 327,236 370,200 600,200 600,343 0,343" fill="var(--brand-blue)"/>
      <polygon points="332,236 343,236 386,200 375,200" fill="var(--brand-grey)"/>
      <line x1="0" y1="236" x2="327" y2="236" stroke="#ffffff" stroke-width="2"/>
    </svg>

    <div class="wordmark"><span class="mark"></span>Dunmore Roofing</div>

    <div class="person">
      <p class="person-name">
        <svg viewBox="0 0 16 16" aria-hidden="true" fill="#fff"><rect x="0" y="0" width="7" height="7"/><rect x="9" y="0" width="7" height="7"/><rect x="0" y="9" width="7" height="7"/><rect x="9" y="9" width="7" height="7"/></svg>
        PAUL DUNMORE
      </p>
      <p class="person-role">OWNER</p>
    </div>

    <p class="address">4172 Township road 43<br>Ashcombe, MR K9X4T2</p>

    <ul class="contacts">
      <li>
        <svg viewBox="0 0 24 24" aria-hidden="true"><path d="M6.6 10.8a15.1 15.1 0 0 0 6.6 6.6l2.2-2.2c.3-.3.7-.4 1-.2 1.1.4 2.3.6 3.6.6.6 0 1 .4 1 1V20c0 .6-.4 1-1 1A17 17 0 0 1 3 4c0-.6.4-1 1-1h3.5c.6 0 1 .4 1 1 0 1.3.2 2.5.6 3.6.1.3 0 .7-.2 1z"/></svg>
        613 555 0147
      </li>
      <li>
        <svg viewBox="0 0 24 24" aria-hidden="true"><path d="M2 5h20v2l-10 6L2 7z"/><path d="M2 9l10 6 10-6v10H2z"/></svg>
        paul@dunmoreroofing-example.com
      </li>
      <li>
        <svg viewBox="0 0 24 24" aria-hidden="true"><circle cx="12" cy="12" r="10"/><path d="M7 8c2 0 3 1 3 3s-2 2-2 4 1 3 1 3M15 5c-1 2 0 3 2 4s3 2 2 4" fill="none" stroke="#1b4589" stroke-width="1.8"/></svg>
        www.dunmoreroofing-example.com
      </li>
    </ul>
  </section>

  <section class="card card-back" aria-label="Business card back">
    <div class="wordmark"><span class="mark"></span>Dunmore Roofing</div>
    <p class="website">www.dunmoreroofing-example.com</p>
  </section>
</body>
</html>
```